Corporate Template

Looking for a set of corporate slides to be made which contain multiple different slides and orientations. Looking for at least 8 to 10 different master pages plus a Coversheet and closeout page. Incorporating a color palate similar to our logo coloring is preferred.
I have attached a logo.
I like the amber quill works designs best so far. They seem to fit what I'm looking for in terms of visual appearance.
Reason: I'm trying to allow time for a couple new designers to incorporate some changes I requested to their existing designs.

```html
<!DOCTYPE html>
<html lang="en">
<head>
<meta charset="utf-8">
<title>Closing Slide</title>
<link rel="stylesheet" href="https://fonts.googleapis.com/css2?family=Titillium+Web:wght@400;600;700&display=swap">
<style>
  :root {
    --brand-blue: #3270ab;
    --brand-deep: #2a64a0;
    --brand-dark: #23578f;
    --brand-light: #62a9e6;
    --brand-pale: #86bdee;
    --ink: #1e1e1e;
    --rule: #e4e4e4;
    --paper: #ffffff;
  }
  * { margin: 0; padding: 0; box-sizing: border-box; }
  html, body { width: 1200px; height: 900px; overflow: hidden; background: var(--paper); }
  body { font-family: "Titillium Web", sans-serif; }

  .slide { position: relative; width: 1200px; height: 900px; overflow: hidden; background: var(--paper); }

  .slide-header {
    position: absolute; left: 0; top: 0; width: 1200px; height: 90px;
    background: linear-gradient(90deg, var(--brand-deep), var(--brand-blue) 60%, var(--brand-deep));
    border-bottom: 7px solid var(--brand-light);
  }
  .slide-title {
    position: absolute; left: 30px; top: 18px;
    color: var(--paper); font-size: 40px; font-weight: 700; line-height: 1.2;
  }
  .header-mark {
    position: absolute; right: 14px; top: 6px; width: 72px; height: 72px;
    border-radius: 50%; border: 4px solid var(--paper);
  }

  .closing-message {
    position: absolute; left: 210px; top: 145px; width: 885px;
    text-align: center; color: var(--brand-blue);
    font-size: 46px; font-weight: 700; line-height: 57px;
  }

  .company-name {
    position: absolute; left: 375px; top: 330px; width: 600px;
    text-align: center; color: var(--brand-blue);
    font-size: 70px; font-weight: 400; line-height: 84px; letter-spacing: 2px;
    white-space: nowrap;
  }

  .rule {
    position: absolute; left: 435px; width: 480px; height: 2px;
    background: linear-gradient(90deg, transparent, var(--rule) 20%, var(--rule) 80%, transparent);
  }
  .rule-top { top: 489px; }
  .rule-bottom { top: 595px; }

  .contact-person { position: absolute; left: 375px; top: 503px; width: 600px; text-align: center; }
  .person-name { color: var(--brand-blue); font-size: 36px; font-weight: 400; line-height: 48px; }
  .person-role { color: var(--ink); font-size: 28px; font-weight: 600; line-height: 36px; }

  .contact-list { position: absolute; left: 500px; top: 612px; list-style: none; }
  .contact-item {
    display: flex; align-items: center; height: 61px;
    color: var(--ink); font-size: 22px; font-weight: 600;
  }
  .contact-icon { width: 36px; height: 36px; margin-right: 16px; flex: none; }

  .slide-footer { position: absolute; left: 0; top: 700px; width: 1200px; height: 200px; }
  .footer-name {
    position: absolute; left: 30px; top: 822px;
    color: var(--paper); font-size: 36px; font-weight: 400; line-height: 44px;
    letter-spacing: 1px; white-space: nowrap;
  }
  .copyright {
    position: absolute; left: 787px; top: 862px;
    color: var(--brand-pale); font-size: 21px; font-weight: 400;
  }
  .page-number {
    position: absolute; left: 1146px; top: 833px; width: 38px; height: 38px;
    border-radius: 50%; border: 2px solid var(--paper); background: var(--brand-dark);
    color: var(--paper); font-size: 15px; font-weight: 700;
    display: flex; align-items: center; justify-content: center;
  }
</style>
</head>
<body>
<main class="slide">
  <header class="slide-header">
    <h1 class="slide-title">Project Title here</h1>
    <div class="header-mark"></div>
  </header>

  <p class="closing-message">Looking forward to hearing from you<br>and&nbsp; thank you for your time!</p>

  <p class="company-name">HALCYON LABS</p>

  <div class="rule rule-top"></div>
  <div class="contact-person">
    <p class="person-name">Company Founder</p>
    <p class="person-role">Co-founder</p>
  </div>
  <div class="rule rule-bottom"></div>

  <ul class="contact-list">
    <li class="contact-item">
      <svg class="contact-icon" viewBox="0 0 36 36" aria-hidden="true">
        <circle cx="18" cy="18" r="18" fill="var(--brand-deep)"/>
        <rect x="9" y="11" width="18" height="14" rx="1.5" fill="none" stroke="#fff" stroke-width="2"/>
        <path d="M9.5 12 L18 19 L26.5 12" fill="none" stroke="#fff" stroke-width="2"/>
      </svg>
      companyfounder@halcyonmail.com
    </li>
    <li class="contact-item">
      <svg class="contact-icon" viewBox="0 0 36 36" aria-hidden="true">
        <circle cx="18" cy="18" r="18" fill="var(--brand-deep)"/>
        <path d="M11 25 l3-4 h10 a2 2 0 0 0 2-2 v-7 a2 2 0 0 0-2-2 h-12 a2 2 0 0 0-2 2 v7 a2 2 0 0 0 2 2 z" fill="#fff"/>
      </svg>
      company.founder
    </li>
    <li class="contact-item">
      <svg class="contact-icon" viewBox="0 0 36 36" aria-hidden="true">
        <circle cx="18" cy="18" r="18" fill="var(--brand-deep)"/>
        <path d="M8 15 q10-7 20 0 l-2 3 -4-1 v-2 q-4-1.5-8 0 v2 l-4 1 z" fill="#fff"/>
        <rect x="11" y="19" width="14" height="7" rx="2" fill="#fff"/>
      </svg>
      +0 123 456 78 01, +0 123 456 78 01
    </li>
  </ul>

  <svg class="slide-footer" viewBox="0 700 1200 200" aria-hidden="true">
    <defs>
      <linearGradient id="footer-fill" x1="0" y1="0" x2="1" y2="0">
        <stop offset="0" stop-color="#2c67a3"/>
        <stop offset="0.5" stop-color="#2a63a0"/>
        <stop offset="1" stop-color="#3a7cbd"/>
      </linearGradient>
    </defs>
    <path d="M0 735 Q600 950 1200 720 L1200 900 L0 900 Z" fill="url(#footer-fill)"/>
    <path d="M0 735 Q600 950 1200 720" fill="none" stroke="var(--brand-light)" stroke-width="5"/>
  </svg>

  <p class="footer-name">HALCYON LABS</p>
  <p class="copyright">Copyright text here</p>
  <div class="page-number">01</div>
</main>
</body>
</html>
```